KTR Design Business Card

I need to develop a business card for my real estate design and investment company. Something clean, classic and professional with a modern vibe.

Industry/Entity Type

Real Estate

Font styles to use
Serif
Sans Serif

```html
<!DOCTYPE html>
<html lang="en">
<head>
<meta charset="utf-8">
<title>KTR Design Business Card</title>
<link href="https://fonts.googleapis.com/css2?family=Michroma&family=Questrial&display=swap" rel="stylesheet">
<style>
  :root {
    --page-bg: #e9e8e6;
    --card-light: #f4f4f4;
    --card-light-edge: #dcdcdc;
    --card-dark: #333334;
    --accent-grey: #b3b3b5;
    --text-dark: #2c2c2c;
    --text-light: #f2f2f2;
  }
  html, body {
    margin: 0;
    width: 1200px;
    height: 900px;
    overflow: hidden;
    background: var(--page-bg);
  }
  .canvas {
    position: relative;
    width: 1200px;
    height: 900px;
  }
  .business-card {
    position: absolute;
    left: 150px;
    top: 190px;
    width: 900px;
    height: 520px;
    border-radius: 38px;
    overflow: hidden;
    box-shadow: 0 18px 40px rgba(0,0,0,0.18);
  }
  .card-shapes {
    position: absolute;
    inset: 0;
  }
  .brand-name {
    position: absolute;
    left: 200px;
    top: 120px;
    margin: 0;
    font-family: "Questrial", sans-serif;
    font-weight: 400;
    font-size: 56px;
    letter-spacing: 6px;
    color: var(--text-dark);
  }
  .contact-person {
    position: absolute;
    right: 470px;
    top: 300px;
    text-align: right;
    font-family: "Michroma", sans-serif;
    color: var(--text-light);
  }
  .person-name {
    margin: 0;
    font-size: 19px;
    letter-spacing: 2px;
    font-weight: 400;
  }
  .person-role {
    margin: 6px 0 0;
    font-size: 13px;
    letter-spacing: 2px;
  }
  .person-address {
    margin: 34px 0 0;
    font-size: 14px;
    letter-spacing: 2px;
    line-height: 1.6;
  }
  .divider {
    position: absolute;
    left: 450px;
    top: 280px;
    width: 1px;
    height: 150px;
    background: var(--text-light);
    opacity: 0.7;
  }
  .contact-list {
    position: absolute;
    left: 470px;
    top: 226px;
    margin: 0;
    padding: 0;
    list-style: none;
    font-family: "Michroma", sans-serif;
    font-size: 15px;
    letter-spacing: 2px;
    color: var(--text-light);
  }
  .contact-list li {
    display: flex;
    align-items: center;
    gap: 10px;
    height: 28px;
  }
  .contact-list .gap-before { margin-top: 18px; }
  .contact-icon { width: 16px; height: 16px; flex: none; }
</style>
</head>
<body>
<div class="canvas">
  <div class="business-card">
    <svg class="card-shapes" viewBox="0 0 900 520" width="900" height="520" aria-hidden="true">
      <defs>
        <linearGradient id="lightFace" x1="0" y1="0" x2="0" y2="1">
          <stop offset="0" stop-color="var(--card-light)"/>
          <stop offset="1" stop-color="var(--card-light-edge)"/>
        </linearGradient>
      </defs>
      <rect width="900" height="520" fill="url(#lightFace)"/>
      <path d="M0,318 C190,322 420,232 610,170 C730,132 830,122 900,128 L900,520 L0,520 Z" fill="var(--accent-grey)"/>
      <path d="M0,345 C200,348 430,256 620,192 C735,154 830,144 900,150 L900,520 L0,520 Z" fill="var(--card-dark)"/>
    </svg>

    <h1 class="brand-name">KTR Design</h1>

    <div class="contact-person">
      <h2 class="person-name">MARCUS HALE</h2>
      <p class="person-role">OWNER / C.E.O</p>
      <p class="person-address">SUITE # 410, VALE BLDG,<br>NY 10482</p>
    </div>

    <div class="divider"></div>

    <ul class="contact-list">
      <li>
        <svg class="contact-icon" viewBox="0 0 16 16"><circle cx="8" cy="8" r="8" fill="var(--text-light)"/><path d="M5 4.5l2 0 0.6 2-1 0.8a5 5 0 0 0 2.1 2.1l0.8-1 2 0.6 0 2a1 1 0 0 1-1 0.9A6 6 0 0 1 4.2 5.5a1 1 0 0 1 0.8-1z" fill="var(--card-dark)"/></svg>
        555-201-4410
      </li>
      <li>
        <svg class="contact-icon" viewBox="0 0 16 16"><circle cx="8" cy="8" r="8" fill="var(--text-light)"/><rect x="5.5" y="3.5" width="5" height="9" rx="1" fill="var(--card-dark)"/></svg>
        555-302-7781
      </li>
      <li>
        <svg class="contact-icon" viewBox="0 0 16 16"><circle cx="8" cy="8" r="8" fill="var(--text-light)"/><rect x="4" y="6" width="8" height="5" rx="1" fill="var(--card-dark)"/><rect x="5.5" y="4" width="5" height="2" fill="var(--card-dark)"/></svg>
        555-618-9025
      </li>
      <li class="gap-before">
        <svg class="contact-icon" viewBox="0 0 16 16"><circle cx="8" cy="8" r="8" fill="var(--text-light)"/><rect x="4" y="5" width="8" height="6" fill="var(--card-dark)"/><path d="M4 5l4 3.5 4-3.5" stroke="var(--text-light)" stroke-width="0.8" fill="none"/></svg>
        INFO@KTRDESIGN.COM
      </li>
      <li>
        <svg class="contact-icon" viewBox="0 0 16 16"><circle cx="8" cy="8" r="8" fill="var(--text-light)"/><circle cx="8" cy="8" r="4.5" stroke="var(--card-dark)" stroke-width="1" fill="none"/><path d="M3.5 8h9M8 3.5c-2 2.5-2 6.5 0 9M8 3.5c2 2.5 2 6.5 0 9" stroke="var(--card-dark)" stroke-width="0.8" fill="none"/></svg>
        WWW.KTRDESIGN.COM
      </li>
    </ul>
  </div>
</div>
</body>
</html>
```